Custom Software Solutions

web design for a small custom programming company in Brisbane Australia. Specialize in business finance solutions, Spreadsheet Automation and programming and data analysis. The design should portray professionalism and honesty. Main applications deal with financial accounting reporting and analysis. Would like to see colors blue and purple used (but sparsely). added file is company logo. Trading name is TR Solutions, while the official company name is TR Solutions (QLD) Pty Ltd.

Target Market(s)

current clients for support
marketing tool for prospective clients

Industry/Entity Type

Business

Number of Pages Required

5+ page

Font styles to use
Sans Serif

Colors
0555a3
a54599
ffffff

Requirements
Must have
• introduction
• blog for news and tips
• previous and current clients/projects page
• contact us page with email submission form
Should not have
• social media links

```html
<!DOCTYPE html>
<html lang="en">
<head>
<meta charset="utf-8">
<title>TR Solutions — Business Finance Solutions</title>
<link href="https://fonts.googleapis.com/css2?family=Source+Sans+3:wght@300;400;600;700&display=swap" rel="stylesheet">
<style>
  :root{
    --blue:#0555a3;
    --purple:#a54599;
    --white:#ffffff;
    --grey-bg:#f5f5f5;
    --text:#777777;
    --nav:#444444;
  }
  *{box-sizing:border-box;margin:0;padding:0}
  html,body{width:858px;height:1200px;overflow:hidden;background:var(--white)}
  body{position:relative;font-family:"Source Sans 3",Arial,sans-serif;color:var(--text)}
  .abs{position:absolute}

  /* hero */
  .hero{left:0;top:0;width:858px;height:444px;
    background:linear-gradient(160deg,#3d6f88 0%,#8fb7c8 35%,#d8e5ea 60%,#eef2f4 100%)}
  .hero-caption{left:418px;top:191px;width:346px;height:154px;background:var(--blue);color:var(--white);padding:26px 31px}
  .hero-caption .kicker{font-size:28px;font-weight:700;line-height:1;letter-spacing:.5px}
  .hero-caption .headline{font-size:27px;font-weight:300;line-height:1;margin-top:9px}
  .hero-caption .sub{font-size:14px;font-weight:400;margin-top:19px}
  .slider-arrow{top:248px;width:42px;height:40px;background:rgba(90,90,90,.75);display:flex;align-items:center;justify-content:center}
  .slider-arrow.prev{left:0}
  .slider-arrow.next{left:818px}

  /* header */
  .site-header{left:94px;top:0;width:670px;height:84px;background:var(--white);box-shadow:0 1px 3px rgba(0,0,0,.15)}
  .brand{left:14px;top:30px;display:flex;align-items:center;gap:8px}
  .brand-mark{width:24px;height:24px;border-radius:50%;background:var(--blue);flex:none}
  .brand-name{font-size:22px;font-weight:400;color:var(--blue);letter-spacing:1px;white-space:nowrap}
  .main-nav a{position:absolute;top:36px;font-size:9.5px;color:var(--nav);text-decoration:none;text-transform:uppercase;white-space:nowrap}
  .main-nav a.active{color:var(--purple);font-weight:600}
  .nav-marker{left:286px;top:0;width:35px;height:2px;background:var(--purple)}

  /* services */
  .services{left:0;top:444px;width:858px;height:296px;background:var(--grey-bg)}
  .service{top:49px;width:230px}
  .service-icon{position:absolute;left:0;top:0;width:48px;height:48px;border-radius:50%;background:var(--blue);display:flex;align-items:center;justify-content:center}
  .service h3{position:absolute;left:55px;top:15px;font-size:14px;font-weight:400;color:var(--blue);white-space:nowrap}
  .service p{position:absolute;left:56px;top:44px;width:156px;font-size:9px;line-height:14.8px;font-weight:400}
  .btn{display:flex;align-items:center;justify-content:center;color:var(--white);font-size:11px;font-weight:700;text-transform:uppercase;box-shadow:0 1px 2px rgba(0,0,0,.25)}
  .btn-purple{background:var(--purple)}
  .btn-blue{background:var(--blue)}

  /* recent solutions */
  .section-title{left:94px;top:769px;font-size:17px;font-weight:400;color:var(--blue)}
  .solution{top:809px;width:207px;text-align:center}
  .solution-photo{width:207px;height:95px;box-shadow:0 2px 2px rgba(0,0,0,.12)}
  .solution h4{margin-top:15px;font-size:14px;font-weight:600;color:var(--purple);white-space:nowrap}
  .solution p{margin:9px 0 0;font-size:9px;line-height:14.8px;font-weight:400}
  .solution .btn{width:74px;height:28px;margin:15px auto 0;font-size:10.5px}

  /* footer */
  .site-footer{left:0;top:1084px;width:858px;height:116px;background:var(--blue);color:var(--white)}
  .footer-col{top:21px}
  .footer-col h5{font-size:12px;font-weight:400;text-transform:uppercase;margin-bottom:7px;white-space:nowrap}
  .footer-col li{list-style:none;font-size:8.5px;line-height:15.5px;font-weight:400;white-space:nowrap}
  .footer-brand{left:630px;top:24px;width:150px;text-align:center}
  .footer-brand .brand-row{display:flex;align-items:center;justify-content:center;gap:6px}
  .footer-brand .brand-mark{background:var(--white);width:20px;height:20px}
  .footer-brand .brand-name{color:var(--white);font-size:16px}
  .footer-brand small{display:block;font-size:8.5px;margin-top:24px;white-space:nowrap;font-weight:400}
</style>
</head>
<body>

  <div class="abs hero" role="img" aria-label="Photo of a hand on a computer mouse with translucent finance charts overlaid"></div>
  <div class="abs hero-caption">
    <div class="kicker">BUSINESS</div>
    <div class="headline">FINANCE SOLUTIONS</div>
    <div class="sub">DONEC PORTA DIAM EU MASSA</div>
  </div>
  <div class="abs slider-arrow prev"><svg width="12" height="16" viewBox="0 0 12 16"><path d="M9 2 3 8l6 6" fill="none" stroke="#fff" stroke-width="3"/></svg></div>
  <div class="abs slider-arrow next"><svg width="12" height="16" viewBox="0 0 12 16"><path d="M3 2l6 6-6 6" fill="none" stroke="#fff" stroke-width="3"/></svg></div>

  <header class="abs site-header">
    <div class="abs nav-marker"></div>
    <div class="abs brand"><span class="brand-mark"></span><span class="brand-name">TR Solutions</span></div>
    <nav class="main-nav">
      <a class="active" style="left:290px">Home</a>
      <a style="left:348px">About</a>
      <a style="left:405px">Blog</a>
      <a style="left:457px">Services</a>
      <a style="left:524px">Solutions</a>
      <a style="left:599px">Contacts</a>
    </nav>
  </header>

  <section class="abs services">
    <div class="abs service" style="left:94px">
      <div class="service-icon"><svg width="22" height="22" viewBox="0 0 22 22" fill="none" stroke="#fff" stroke-width="2"><rect x="2" y="2" width="8" height="8"/><rect x="12" y="2" width="8" height="8"/><rect x="2" y="12" width="8" height="8"/><rect x="12" y="12" width="8" height="8"/></svg></div>
      <h3>Spreadsheet Automation</h3>
      <p>Aenean sollicitudin, lorem quis bibendum auctor, nisi elit consequat ipsum, nec sagittis sem nibh id elit.Duis sed odio sit amet nibh vulputate cursus a sit amet mauris.</p>
    </div>
    <div class="abs service" style="left:322px">
      <div class="service-icon"><svg width="24" height="20" viewBox="0 0 24 20" fill="none" stroke="#fff" stroke-width="2.4"><path d="M7 4 2 10l5 6M17 4l5 6-5 6M14 2l-4 16"/></svg></div>
      <h3>Programming</h3>
      <p>Aenean sollicitudin, lorem quis bibendum auctor, nisi elit consequat ipsum, nec sagittis sem nibh id elit.Duis sed odio sit amet nibh vulputate cursus a sit amet mauris.</p>
    </div>
    <div class="abs service" style="left:554px">
      <div class="service-icon"><svg width="26" height="26" viewBox="0 0 26 26"><circle cx="13" cy="13" r="11" fill="#fff"/><path d="M13 13V2a11 11 0 0 1 11 11z" fill="#0555a3"/></svg></div>
      <h3>Data Analysis</h3>
      <p>Aenean sollicitudin, lorem quis bibendum auctor, nisi elit consequat ipsum, nec sagittis sem nibh id elit.Duis sed odio sit amet nibh vulputate cursus a sit amet mauris.</p>
    </div>
    <div class="abs btn btn-purple" style="left:302px;top:212px;width:115px;height:34px">View All</div>
    <div class="abs btn btn-blue" style="left:440px;top:212px;width:114px;height:34px">Contact Me</div>
  </section>

  <h2 class="abs section-title">RECENT SOLUTIONS</h2>

  <article class="abs solution" style="left:94px">
    <div class="solution-photo" role="img" aria-label="Photo of a hand signing a document with a pen" style="background:linear-gradient(135deg,#cfe3f2,#eef3f7)"></div>
    <h4>Nam Elit Agna Endrerit Sit Amet</h4>
    <p>Aenean sollicitudin, lorem quis bibendum auc nisi elit lconsequat ipsum, nec sagittis sem nibh id elit.Duis sed odio sit amet nibh vulputate</p>
    <div class="btn btn-blue">Details</div>
  </article>
  <article class="abs solution" style="left:326px">
    <div class="solution-photo" role="img" aria-label="Photo of a finger touching a screen of program code" style="background:linear-gradient(135deg,#d9ecc9,#f1f6e8)"></div>
    <h4>Nam Elit Agna Endrerit Sit Amet</h4>
    <p>Aenean sollicitudin, lorem quis bibendum auc nisi elit lconsequat ipsum, nec sagittis sem nibh id elit.Duis sed odio sit amet nibh vulputate</p>
    <div class="btn btn-blue">Details</div>
  </article>
  <article class="abs solution" style="left:557px">
    <div class="solution-photo" role="img" aria-label="Photo of a hand drawing on a data analysis chart" style="background:linear-gradient(135deg,#4a3f5c,#8a7fa8)"></div>
    <h4>Nam Elit Agna Endrerit Sit Amet</h4>
    <p>Aenean sollicitudin, lorem quis bibendum auc nisi elit lconsequat ipsum, nec sagittis sem nibh id elit.Duis sed odio sit amet nibh vulputate</p>
    <div class="btn btn-blue">Details</div>
  </article>

  <footer class="abs site-footer">
    <div class="abs footer-col" style="left:94px">
      <h5>Contact Us</h5>
      <ul><li>hello@tr-solutions.example</li><li>+61-4-00123456 (intl)</li><li>0400 123 456 (within Australia)</li></ul>
    </div>
    <div class="abs footer-col" style="left:288px">
      <h5>Quick Links</h5>
      <ul><li>Nulla Facilisi</li><li>Aenean Nec Eros</li><li>Vestibulum Ante Ipsum Primis</li></ul>
    </div>
    <div class="abs footer-col" style="left:463px">
      <h5>Latest Articles</h5>
      <ul><li>Suspendisse sollicitudin velit sed</li><li>Ut pharetra augue nec augue</li><li>Nam elit agna endrerit sit amet</li></ul>
    </div>
    <div class="abs footer-brand">
      <div class="brand-row"><span class="brand-mark"></span><span class="brand-name">TR Solutions</span></div>
      <small>Copyright © all rights are reserved</small>
    </div>
  </footer>

</body>
</html>
```